Full Page Tolver 250 Ad

We need a full page magazine ad. Our company is a site construction company - meaning we build lakes, ponds, do brush clearing for farmers and ranchers. For commercial customers, we build building pads, site clearing, pavement and soil stabilization. The final design should show what we do. Our website is www.pendrowgrading.com

```html
<!DOCTYPE html>
<html lang="en">
<head>
<meta charset="utf-8">
<title>Tolver 250 – Full Page Ad</title>
<link href="https://fonts.googleapis.com/css2?family=Anton&family=Poppins:wght@400;500;600;700&family=Oswald:wght@500;600;700&display=swap" rel="stylesheet">
<style>
  :root{
    --gold:#e2a62c;
    --gold-deep:#c98f1c;
    --gold-light:#f2b840;
    --ink:#0d0d0d;
    --white:#ffffff;
    --sky:#5ec8e8;
    --sky-soft:#a9dbee;
    --earth:#6e5838;
    --earth-dark:#3a2c1a;
    --silver:#e4e4e8;
  }
  *{box-sizing:border-box;margin:0;padding:0}
  html,body{width:1200px;height:2319px;overflow:hidden;background:#ffffff}
  .ad{
    position:absolute;left:76px;top:481px;width:1048px;height:1357px;
    background:var(--ink);overflow:hidden;
    box-shadow:0 18px 40px rgba(0,0,0,.35);
    font-family:'Poppins',sans-serif;color:var(--white);
  }
  .abs{position:absolute}
  .photo-left{left:0;top:150px;width:560px;height:900px;
    background:linear-gradient(180deg,var(--sky) 0%,var(--sky-soft) 38%,#9fb9a0 50%,#7b8a55 56%,#8c7350 66%,var(--earth) 80%,var(--earth-dark) 100%)}
  .photo-right{left:530px;top:150px;width:518px;height:900px;
    background:linear-gradient(180deg,#7fb3e6 0%,#d5e4f2 32%,#6f8656 54%,#e0c43a 64%,#a29b3f 74%,#6d6a3a 86%,var(--earth-dark) 100%)}
  .fade-bottom{left:0;top:780px;width:1048px;height:300px;
    background:linear-gradient(180deg,rgba(13,13,13,0) 0%,rgba(13,13,13,.55) 55%,var(--ink) 100%)}
  .header-band{left:0;top:0;width:1048px;height:200px}
  .header-stars{top:46px;height:26px;font-size:24px;line-height:26px;color:var(--white);letter-spacing:12px;white-space:nowrap}
  .header-stars.left{left:246px}
  .header-stars.right{left:646px}
  .header-kicker{left:424px;top:38px;width:202px;height:44px;text-align:center;font-family:'Poppins',sans-serif;font-weight:700;font-size:44px;line-height:44px;color:var(--ink);letter-spacing:3px}
  .header-title{left:0;top:86px;width:1048px;text-align:center;font-family:'Anton',sans-serif;font-size:74px;color:var(--ink);letter-spacing:1px;line-height:1;white-space:nowrap}
  .panel-title{font-family:'Anton',sans-serif;font-size:46px;line-height:42px;color:var(--ink);text-align:center;letter-spacing:1.5px;white-space:nowrap}
  .panel-title.left{left:100px;top:234px;width:380px}
  .panel-title.right{left:570px;top:234px;width:420px}
  .circle{width:174px;height:174px;border-radius:50%;border:2px solid #1b2a38;padding:4px;background:rgba(255,255,255,.35)}
  .circle span{display:block;width:100%;height:100%;border-radius:50%}
  .c1{left:93px;top:326px}.c1 span{background:linear-gradient(180deg,#8bb9d4,#4f6a4a 45%,#8bb060 70%,#6a8a3a)}
  .c2{left:298px;top:326px}.c2 span{background:linear-gradient(180deg,#c6dbe7,#7b8f7e 40%,#6e8f5a 60%,#5c6f78)}
  .c3{left:583px;top:340px}.c3 span{background:linear-gradient(180deg,#b9c7d3,#a38e6a 40%,#8f7d61 70%,#6d604b)}
  .c4{left:790px;top:340px}.c4 span{background:linear-gradient(180deg,#7da6d4,#c7d8e6 35%,#6d8c90 48%,#8a7558 62%,#6a5a46)}
  .ribbon{left:370px;top:843px;width:308px;height:30px}
  .ribbon-text{left:370px;top:843px;width:308px;height:30px;line-height:30px;text-align:center;font-family:'Anton',sans-serif;font-size:15px;letter-spacing:4px;color:var(--ink)}
  .oilfield{left:0;top:882px;width:1048px;text-align:center;font-family:'Poppins',sans-serif;font-weight:700;font-size:30px;line-height:40px;color:var(--gold-light);letter-spacing:.5px}
  .tagline{left:0;top:922px;width:1048px;text-align:center;font-family:'Anton',sans-serif;font-size:23px;line-height:30px;letter-spacing:2.4px;color:var(--white)}
  .group-head{height:38px;line-height:38px;border-radius:8px 8px 0 0;text-align:center;font-family:'Oswald',sans-serif;font-weight:600;font-size:18px;color:var(--ink);
    background:linear-gradient(180deg,#ffffff,var(--silver) 60%,#c9c9cf)}
  .group-head.farm{left:92px;top:967px;width:363px}
  .group-head.commercial{left:475px;top:967px;width:485px}
  .tile{top:1007px;height:106px;width:118px;background:linear-gradient(180deg,var(--gold-light),var(--gold-deep));border-radius:0 0 8px 8px;
    text-align:center;color:var(--ink);font-weight:500;font-size:15px;line-height:1.15;padding-top:14px}
  .tile svg{display:block;margin:0 auto 8px;width:34px;height:34px}
  .brand{left:100px;top:1160px;width:320px;height:110px;display:flex;align-items:center;gap:16px}
  .brand-mark{width:40px;height:40px;background:var(--gold)}
  .brand-name{font-family:'Poppins',sans-serif;font-weight:700;font-size:48px;color:var(--white);line-height:1}
  .contact-head{left:465px;top:1150px;width:520px;font-family:'Poppins',sans-serif;font-size:32px;line-height:44px;font-weight:400;letter-spacing:.3px;white-space:nowrap}
  .contact-head b{color:var(--gold-light);font-weight:700}
  .contact-rule{left:466px;top:1200px;width:496px;height:1px;background:#9a9a9a}
  .contact-line{left:466px;top:1209px;width:520px;font-weight:500;font-size:16px;display:flex;gap:26px;align-items:center}
  .contact-line span{display:flex;align-items:center;gap:7px}
  .contact-line svg{width:15px;height:15px}
  .url-pill{left:460px;top:1244px;width:508px;height:46px;border-radius:12px;background:var(--gold-light);text-align:center;line-height:46px;
    color:var(--ink);font-size:28px;letter-spacing:3px}
  .url-pill b{font-weight:700}
</style>
</head>
<body>
<main class="ad">
  <div class="abs photo-left" role="img" aria-label="Farm and ranch photo: tractor pulling a scraper across freshly graded soil under a blue sky with oak trees"></div>
  <div class="abs photo-right" role="img" aria-label="Commercial site photo: yellow compactor with wide sheepsfoot roller on a brush-cleared site"></div>
  <svg class="abs" style="left:500px;top:170px" width="80" height="880" viewBox="0 0 80 880" aria-hidden="true">
    <polyline points="36,0 40,40 30,90 38,140 28,200 36,260 26,330 34,400 24,470 32,540 22,610 30,680 20,750 28,820 22,880" fill="none" stroke="#f4f4f4" stroke-width="4"/>
  </svg>
  <div class="abs fade-bottom"></div>

  <svg class="abs header-band" viewBox="0 0 1048 200" aria-hidden="true">
    <polygon fill="#f4f4f4" points="0,0 1048,0 1048,186 1010,180 985,190 950,176 920,188 880,178 840,192 800,180 760,186 720,176 690,188 650,182 610,194 570,180 535,186 500,178 460,190 420,180 380,188 340,176 300,190 260,180 220,186 180,176 140,190 100,180 60,188 30,178 0,186"/>
    <polygon fill="#e2a62c" points="0,0 1048,0 1048,178 1010,172 985,182 950,168 920,180 880,170 840,184 800,172 760,178 720,168 690,180 650,174 610,186 570,172 535,178 500,170 460,182 420,172 380,180 340,168 300,182 260,172 220,178 180,168 140,182 100,172 60,180 30,170 0,178"/>
  </svg>
  <div class="abs header-stars left" aria-hidden="true">★★★★★</div>
  <div class="abs header-kicker">TEXAS</div>
  <div class="abs header-stars right" aria-hidden="true">★★★★★★</div>
  <div class="abs header-title">SITE CONSTRUCTION COMPANY</div>

  <div class="abs panel-title left">FARM &amp; RANCH<br>PROJECTS</div>
  <div class="abs panel-title right">COMMERCIAL SITE<br>CONSTRUCTION</div>

  <div class="abs circle c1" role="img" aria-label="Ranch lake with wild turkeys on the grassy shore"><span></span></div>
  <div class="abs circle c2" role="img" aria-label="Aerial view of a new pond with a grassy peninsula"><span></span></div>
  <div class="abs circle c3" role="img" aria-label="Scraper and tractor working on a commercial pad"><span></span></div>
  <div class="abs circle c4" role="img" aria-label="Tractor grading a waterfront commercial site"><span></span></div>

  <svg class="abs ribbon" viewBox="0 0 308 30" aria-hidden="true">
    <polygon points="0,0 308,0 288,15 308,30 0,30 20,15" fill="#ececec"/>
  </svg>
  <div class="abs ribbon-text">50 YEARS EXPERIENCE</div>
  <div class="abs oilfield">WE ALSO DO OILFIELD SERVICES</div>
  <div class="abs tagline">TOLVER 250 IS THE ANSWER TO YOUR PROJECT NEEDS</div>

  <div class="abs group-head farm">FOR FARMERS AND RANCHERS WE BUILD</div>
  <div class="abs group-head commercial">FOR COMMERCIAL CUSTOMERS WE BUILD</div>

  <div class="abs tile" style="left:92px">
    <svg viewBox="0 0 34 34"><path d="M4 24c5-4 10 4 15 0s10 4 12 0" fill="none" stroke="#1a1a1a" stroke-width="3"/><path d="M10 6l5 8H5z M22 4l6 10H16z" fill="#1a1a1a"/></svg>Lakes</div>
  <div class="abs tile" style="left:214px">
    <svg viewBox="0 0 34 34"><ellipse cx="17" cy="22" rx="14" ry="7" fill="#1a1a1a"/><path d="M17 6v10M13 10h8" stroke="#1a1a1a" stroke-width="3"/></svg>Ponds</div>
  <div class="abs tile" style="left:337px">
    <svg viewBox="0 0 34 34"><path d="M24 3l7 7-9 9-7-7z" fill="#1a1a1a"/><path d="M14 14l6 6-10 11-7-7z" fill="#1a1a1a"/></svg>Brush<br>clearing</div>

  <div class="abs tile" style="left:475px">
    <svg viewBox="0 0 34 34"><path d="M3 31h28M6 31V6h14v25M10 10h6M10 15h6M10 20h6M22 31V16h8v15" fill="none" stroke="#1a1a1a" stroke-width="2.6"/></svg>Building<br>pads</div>
  <div class="abs tile" style="left:597px">
    <svg viewBox="0 0 34 34"><path d="M17 2v16" stroke="#1a1a1a" stroke-width="3"/><path d="M10 18h14l3 14H7z" fill="#1a1a1a"/></svg>Site<br>clearing</div>
  <div class="abs tile" style="left:719px">
    <svg viewBox="0 0 34 34"><path d="M3 6h28M3 13h28M3 20h28M3 27h28M6 3v28M13 3v28M20 3v28M27 3v28" stroke="#1a1a1a" stroke-width="2.4" stroke-dasharray="3 2"/></svg>Pavement<br>stabilization</div>
  <div class="abs tile" style="left:842px">
    <svg viewBox="0 0 34 34"><rect x="3" y="5" width="28" height="5" fill="#1a1a1a"/><rect x="3" y="14" width="28" height="5" fill="#1a1a1a"/><rect x="3" y="23" width="28" height="5" fill="#1a1a1a"/></svg>Soil<br>stabilization</div>

  <div class="abs brand"><div class="brand-mark"></div><div class="brand-name">Tolver 250</div></div>

  <div class="abs contact-head">CONTACT US FOR <b>AN ESTIMATE</b></div>
  <div class="abs contact-rule"></div>
  <div class="abs contact-line">
    <span><svg viewBox="0 0 16 16"><circle cx="8" cy="8" r="8" fill="#e2a62c"/><path d="M5 4l2 2-1 1.5c.6 1.3 1.3 2 2.5 2.5L10 9l2 2-1.5 1.5C7 12 4 9 3.5 5.5z" fill="#0d0d0d"/></svg>555.010-2663</span>
    <span><svg viewBox="0 0 16 16"><path d="M8 1a5 5 0 0 1 5 5c0 4-5 9-5 9S3 10 3 6a5 5 0 0 1 5-5z" fill="#e2a62c"/><circle cx="8" cy="6" r="2" fill="#0d0d0d"/></svg>PO Box 412, Marlow Creek, TX 78000, US</span>
  </div>
  <div class="abs url-pill">www.<b>pendrowgrading</b>.com</div>
</main>
</body>
</html>
```